Business card design

We need a business card designed completed for a new company. We are a company that works with associations, schools to convert their older text/DVDs into dynamic online and mobile programs. Our initial platform is designed for the legal associations and will enable their lawyers to access their content such as forms, videos, case law and support materials anywhere, anytime. We are also focused on Project Management Associations, Financial Management Associations and IT Associations.

I would like for the business card to have the following information:

Logo

Kent marrowby

President and CEO

kmarrowby@trevantiq.example

Mobile: 555-374-9160

www.trevantiq.example

Tag line: Transforming content into a mobile platform    

I would like it to be double sided, use the colours of the logo, tie into the mobile world

 

Industry/Entity Type

Legal

Logo Text

Trevantiq

```html
<!DOCTYPE html>
<html lang="en">
<head>
<meta charset="utf-8">
<title>Trevantiq Business Card Set</title>
<link rel="stylesheet" href="https://fonts.googleapis.com/css2?family=Open+Sans:wght@400;600;700&display=swap">
<style>
  :root {
    --stage: #e4e1dc;
    --card-grey: #8e8e8e;
    --card-white: #ffffff;
    --bar-dark: #666666;
    --bar-light: #9a9a9a;
    --ink: #151515;
    --ink-soft: #444444;
    --name-on-white: #6a6a6a;
    --logo-on-white: #5e5e5e;
    --white: #ffffff;
  }
  * { margin: 0; padding: 0; box-sizing: border-box; }
  html, body { width: 1200px; height: 800px; overflow: hidden; }
  body {
    position: relative;
    background: var(--stage);
    font-family: "Open Sans", Arial, sans-serif;
    color: var(--ink);
  }
  .side-label {
    position: absolute;
    width: 200px;
    text-align: center;
    font-size: 21px;
    color: #111;
  }
  .card {
    position: absolute;
    width: 509px;
    height: 290px;
    border-radius: 18px;
    overflow: hidden;
    box-shadow: 0 4px 10px rgba(0,0,0,.25);
  }
  .card--grey { background: var(--card-grey); }
  .card--white { background: var(--card-white); }

  .bar { position: absolute; top: 43px; height: 53px; }
  .bar--lead { left: 0; width: 55px; background: var(--bar-dark); }
  .bar--tail-box { right: 0; width: 136px; background: var(--white); border: 1px solid #555; border-right: none; }
  .bar--tail-grey { right: 0; width: 135px; background: var(--bar-light); }

  .wordmark {
    position: absolute;
    font-weight: 700;
    line-height: 1;
    letter-spacing: -1px;
  }
  .card--grey .wordmark { color: var(--white); }
  .card--white .wordmark { color: var(--logo-on-white); }
  .wordmark--header { left: 65px; top: 40px; font-size: 52px; }
  .wordmark--hero { left: 0; right: 0; top: 100px; text-align: center; font-size: 78px; }

  .tagline { position: absolute; left: 62px; top: 112px; font-size: 14.5px; }

  .contact-block { position: absolute; left: 65px; top: 184px; }
  .person { font-size: 15px; font-weight: 700; margin-bottom: 6px; }
  .card--grey .person { color: var(--white); }
  .card--white .person { color: var(--name-on-white); }
  .person .role { font-size: 13px; font-weight: 400; }
  .contact-list { list-style: none; font-size: 13px; }
  .contact-list li { display: flex; align-items: center; height: 21px; }
  .contact-list svg { width: 10px; height: 10px; margin-right: 9px; fill: var(--ink-soft); }

  .web-footer {
    position: absolute;
    left: 0; right: 0; bottom: 18px;
    text-align: center;
    font-size: 17px;
    letter-spacing: 4px;
    color: var(--ink);
  }
</style>
</head>
<body>

  <div class="side-label" style="left:229px; top:48px;">Front</div>
  <div class="side-label" style="left:787px; top:48px;">Back - 1</div>
  <div class="side-label" style="left:229px; top:408px;">Back - 2</div>
  <div class="side-label" style="left:787px; top:408px;">Back - 3</div>

  <!-- Front -->
  <section class="card card--grey" style="left:73px; top:90px;">
    <div class="bar bar--lead"></div>
    <div class="wordmark wordmark--header">Trevantiq</div>
    <div class="bar bar--tail-box"></div>
    <p class="tagline">Transforming content into a mobile platform</p>
    <div class="contact-block">
      <p class="person">Kent marrowby, <span class="role">President and CEO</span></p>
      <ul class="contact-list">
        <li><svg viewBox="0 0 10 10"><rect x="2.5" y="0" width="5" height="10" rx="1"/></svg>555-374-9160</li>
        <li><svg viewBox="0 0 10 10"><path d="M0 3 L5 0 L10 3 V9 H0 Z"/></svg>kmarrowby@trevantiq.example</li>
        <li><svg viewBox="0 0 10 10"><circle cx="5" cy="5" r="4.5" fill="none" stroke="#444" stroke-width="1"/><path d="M0.5 5 H9.5 M5 0.5 V9.5" stroke="#444" stroke-width="0.8"/></svg>www.trevantiq.example</li>
      </ul>
    </div>
  </section>

  <!-- Back 1 -->
  <section class="card card--white" style="left:638px; top:90px;">
    <div class="bar bar--lead"></div>
    <div class="wordmark wordmark--header">Trevantiq</div>
    <div class="bar bar--tail-grey"></div>
    <p class="tagline">Transforming content into a mobile platform</p>
    <div class="contact-block">
      <p class="person">Kent marrowby, <span class="role">President and CEO</span></p>
      <ul class="contact-list">
        <li><svg viewBox="0 0 10 10"><rect x="2.5" y="0" width="5" height="10" rx="1"/></svg>555-374-9160</li>
        <li><svg viewBox="0 0 10 10"><path d="M0 3 L5 0 L10 3 V9 H0 Z"/></svg>kmarrowby@trevantiq.example</li>
        <li><svg viewBox="0 0 10 10"><circle cx="5" cy="5" r="4.5" fill="none" stroke="#444" stroke-width="1"/><path d="M0.5 5 H9.5 M5 0.5 V9.5" stroke="#444" stroke-width="0.8"/></svg>www.trevantiq.example</li>
      </ul>
    </div>
  </section>

  <!-- Back 2 -->
  <section class="card card--grey" style="left:73px; top:452px;">
    <div class="wordmark wordmark--hero">Trevantiq</div>
    <p class="web-footer">www.trevantiq.example</p>
  </section>

  <!-- Back 3 -->
  <section class="card card--white" style="left:634px; top:450px;">
    <div class="wordmark wordmark--hero">Trevantiq</div>
    <p class="web-footer">www.trevantiq.example</p>
  </section>

</body>
</html>
```